institute for female grief councelors needs a design for its facebook group

Each year about 350.000 German women do have a misscarriage while they are pregnant. Their pain and grief is soul deep. Lots of them are stay still in grief even if they have got other children who are healthy and alive. Lots of these women have got difficulty in finally letting go pain, rage and grief. Some are even still in grief after more than twenty or thirty years of having lost their child through misscarriage!!!!

With this facebook group I want to give hope, trust and support as well as helpful advice in coping with this deep soul pain after having lost your child through misscarriage.

The facebook cover shall cause a great curiosity and fascination to the mothers so that they are interested in joining our facebook group.

At our institute women can book a-one-year-training to become a certified "Coach for BirkenFeen" (grief councelor for women who are in deep grief after their misscarriage).

In Germany children who died through misscarriage are named "Sternenkind" (STARCHILD).
Therefore I want to have at least one shing star at the facebook cover symbolizing the still shining soullight of the dead child watching its mother who is still living on earth.

On the left side of the uploaded file you see the planet venus: symbol for mothers / female side of life.
The red sky colour symbolizes the colour of the uterus, the embryo's home before having died through misscarriage.
It ist also possible to include the silhoutte of a mother / several mothers looking up into the red / blue sky to watch the shining soullight of their dead child.

The facebook cover MUST include the following sentence:

Mama, ich lasse mein Licht für dich leuchten

(Mummy, I let my soullight shine for you)

Low design quality

Target Market(s)

German speaking mothers

Industry/Entity Type

coaching

Font styles to use
Script

Colors

Designer to choose colors to be used in the design.

Requirements
Must have
• golden fond writing, at least one shing star, silhouette of one / several mothers (no model typa - normal woman)
Nice to have
• planet venus - red background cover (like uterus colour)
Should not have
• mothers who like like a model or filmstar

```html
<!DOCTYPE html>
<html lang="de">
<head>
<meta charset="utf-8">
<title>Mama, ich lasse mein Licht für dich leuchten</title>
<link rel="stylesheet" href="https://fonts.googleapis.com/css2?family=Allura&display=swap">
<style>
  :root {
    --night-deep: #120f2e;
    --night-violet: #2e1f5c;
    --dusk-purple: #5a2f72;
    --uterus-red: #a8384c;
    --glow-rose: #f08a7a;
    --starlight: #fff6ea;
    --venus-light: #fdf0d6;
    --venus-warm: #efd09c;
    --venus-edge: #d39a5c;
    --silhouette: 5, 3, 8;
    --gold: #e9c25a;
  }
  html, body {
    margin: 0;
    padding: 0;
    width: 1200px;
    height: 676px;
    overflow: hidden;
    background: var(--night-deep);
  }
  .cover {
    position: relative;
    width: 1200px;
    height: 676px;
    overflow: hidden;
    background:
      radial-gradient(ellipse 460px 300px at 950px 140px, rgba(240,138,122,.8), rgba(168,56,76,.45) 50%, transparent 80%),
      radial-gradient(ellipse 80px 50px at 600px 295px, rgba(190,60,70,.6), transparent 80%),
      radial-gradient(ellipse 220px 160px at 40px 500px, rgba(168,56,76,.55), transparent 75%),
      linear-gradient(115deg, var(--night-deep) 0%, var(--night-violet) 40%, var(--dusk-purple) 68%, var(--uterus-red) 100%);
  }
  .starfield {
    position: absolute;
    inset: 0;
    background-image:
      radial-gradient(circle, rgba(255,255,255,.95) 0 1.2px, transparent 1.8px),
      radial-gradient(circle, rgba(255,235,245,.8) 0 0.9px, transparent 1.4px),
      radial-gradient(circle, rgba(210,220,255,.85) 0 1px, transparent 1.5px),
      radial-gradient(circle, rgba(255,255,255,.6) 0 0.7px, transparent 1.2px),
      radial-gradient(circle, rgba(255,255,255,.9) 0 1.6px, transparent 2.2px);
    background-size: 97px 83px, 53px 61px, 71px 47px, 29px 37px, 211px 173px;
    background-position: 0 0, 17px 29px, 41px 11px, 7px 19px, 90px 60px;
  }
  .soul-star {
    position: absolute;
    left: 790px;
    top: 10px;
    width: 330px;
    height: 250px;
    border-radius: 50%;
    background: radial-gradient(circle at 50% 50%, var(--starlight) 0%, rgba(255,230,210,.85) 14%, rgba(240,138,122,.35) 42%, transparent 70%);
  }
  .sparkle {
    position: absolute;
    left: 1063px;
    top: 22px;
  }
  .venus {
    position: absolute;
    left: 99px;
    top: 139px;
    width: 494px;
    height: 490px;
    border-radius: 50%;
    background: radial-gradient(circle at 48% 40%, var(--venus-light) 0%, var(--venus-warm) 65%, var(--venus-edge) 100%);
  }
  .mothers {
    position: absolute;
    left: 110px;
    top: 388px;
    width: 475px;
    height: 288px;
    border-radius: 50% 50% 0 0 / 40% 40% 0 0;
    background: linear-gradient(180deg, rgba(var(--silhouette), 0) 0%, rgba(var(--silhouette), .55) 30%, rgba(var(--silhouette), .9) 75%, rgba(var(--silhouette), .95) 100%);
  }
  .swash {
    position: absolute;
    left: 652px;
    top: 314px;
  }
  .message {
    position: absolute;
    margin: 0;
    font-family: "Allura", cursive;
    font-weight: 400;
    color: var(--gold);
    white-space: nowrap;
    line-height: 1;
  }
  .message-address {
    left: 882px;
    top: 292px;
    font-size: 76px;
  }
  .message-promise {
    left: 618px;
    top: 382px;
    font-size: 44px;
  }
</style>
</head>
<body>
  <main class="cover">
    <div class="starfield" aria-hidden="true"></div>
    <div class="soul-star" role="img" aria-label="Hell leuchtender Stern, das Seelenlicht des Sternenkindes"></div>

    <svg class="sparkle" width="110" height="110" viewBox="0 0 110 110" aria-hidden="true">
      <g fill="#ffffff">
        <polygon points="55,0 58,52 55,110 52,52"/>
        <polygon points="0,54 55,51 110,56 55,58"/>
        <polygon points="30,30 56,53 80,80 53,56" opacity=".7"/>
        <polygon points="82,26 57,56 28,84 53,52" opacity=".7"/>
        <circle cx="55" cy="55" r="7"/>
        <polygon points="18,26 19.5,31 24,32 19.5,33 18,38 16.5,33 12,32 16.5,31"/>
        <polygon points="92,22 93.5,27 98,28 93.5,29 92,34 90.5,29 86,28 90.5,27"/>
        <polygon points="88,88 89,91 92,92 89,93 88,96 87,93 84,92 87,91"/>
      </g>
    </svg>

    <div class="venus" role="img" aria-label="Großer cremefarben leuchtender Planet Venus"></div>
    <div class="mothers" role="img" aria-label="Silhouetten dreier Mütter, die zum Himmel hinaufschauen"></div>

    <svg class="swash" width="240" height="60" viewBox="0 0 240 60" aria-hidden="true">
      <path d="M5 50 C 70 56, 160 42, 232 36" fill="none" stroke="var(--gold)" stroke-width="2" stroke-linecap="round"/>
      <circle cx="36" cy="8" r="2.5" fill="var(--gold)"/>
      <circle cx="22" cy="22" r="1.8" fill="var(--gold)"/>
      <circle cx="50" cy="22" r="1.8" fill="var(--gold)"/>
      <circle cx="30" cy="34" r="1.8" fill="var(--gold)"/>
      <circle cx="44" cy="34" r="1.8" fill="var(--gold)"/>
    </svg>

    <h1 class="message message-address">Mama,</h1>
    <p class="message message-promise">ich lasse mein Licht für dich leuchten</p>
  </main>
</body>
</html>
```